Marla’s Sandwich Corner Grand Opening Door Flyer

1. Project Title
• “Flyer Design for Sandwich Shop Grand Opening”
• Why it’s effective: Direct and to the point, highlighting the purpose of the design.

2. Project Description
• “We’re looking for a professional designer to create a vibrant and modern flyer for our sandwich shop, Marla’s Corner. The flyer should emphasize our handcrafted sandwiches, fresh-baked bread, and house-made meats. As a women & family-owned business, we want this aspect prominently displayed. The flyer should also include our logo, a ‘Grand Opening’ and our website: MarlasCorner.example. We want the design to be clean, bold, and visually appealing to attract customers. We also would like a QR code so they can scan to load of the website to order online, but also list it.
• Why it’s effective: Clear goals, modern style preference, and necessary details outlined.

3. Visual Style
• “Modern, bold, and clean design with bright, appetizing colors. Focus on high-quality imagery of sandwiches, sleek fonts, and an inviting layout.”
• Why it’s effective: Communicates the desired aesthetic and tone.

4. Key Details to Include
• Business Name: Marla’s Sandwich Corner
• Taglines:
“Women & Family Owned”
“Handcrafted Sandwiches Made with Love”
“Fresh Baked Bread”
“House-made Slow Roasted House Specialties”
“Gluten-Friendly”
“Vegan-Friendly”
“7:00am Fresh Daily Grounded Coffee and Breakfast”

• Call-to-Action: “Order Online at MarlasCorner.example”
• Placeholder for the logo.
• Size: 4.25 x 11 (Door Hanger)
• File Format: High-resolution PDF, JPEG, or PNG.
• Print-Ready: Include bleed margins and ensure print clarity.

6. Tone
• Friendly and professional. Highlighting that your business is women-owned adds a unique and personal touch vs deli meat shops. We are a gourmet sandwich shop, with fresh baked bread, house-made meats, with gluten and vegan options. Each sandwich is made with love.

Target Market(s)

Coffee drinkers for morning crowd and sandwiches for lunch

Industry/Entity Type

Sandwich Shop

Colors
EB3D1F
EC4F4E
F09395
F8D3D4
FCEDEE

Requirements
Must have
• See Description
Nice to have
• Use website to get a feel for color theme
Should not have
• NA

```html
<!DOCTYPE html>
<html lang="en">
<head>
<meta charset="utf-8">
<title>Marla’s Sandwich Corner – Grand Opening Door Hanger</title>
<link rel="stylesheet" href="https://fonts.googleapis.com/css2?family=Fraunces:ital,opsz,wght@0,9..144,600;0,9..144,700;1,9..144,700;1,9..144,800&family=Open+Sans:wght@400;600;700&display=swap">
<style>
  :root {
    --stage: #545454;
    --ink: #111111;
    --orange: #EB3D1F;
    --coral: #EC4F4E;
    --rose: #F09395;
    --blush: #F8D3D4;
    --petal: #FCEDEE;
    --white: #ffffff;
    --label: #f2f2f2;
  }
  * { margin: 0; padding: 0; box-sizing: border-box; }
  html, body { width: 1200px; height: 900px; overflow: hidden; }
  body { background: var(--stage); font-family: "Open Sans", Arial, sans-serif; position: relative; }

  .hanger {
    position: absolute; top: 97px; width: 255px; height: 660px;
    overflow: hidden; box-shadow: 0 2px 8px rgba(0,0,0,.35);
  }
  .hanger--pink { left: 331px; --paper: var(--blush); --paper-glow: var(--petal); }
  .hanger--white { left: 672px; --paper: var(--white); --paper-glow: #fde9ea; }

  .hanger__shape { position: absolute; inset: 0; }

  .brand {
    position: absolute; left: 24px; top: 16px; color: var(--orange);
    font-family: "Open Sans", Arial, sans-serif; font-weight: 700; line-height: 1;
  }
  .brand__name { display: block; font-size: 21px; letter-spacing: -.5px; }
  .brand__sub { display: block; font-size: 6.5px; letter-spacing: .6px; margin-top: 2px; text-transform: uppercase; }

  .headline { position: absolute; left: 8px; top: 134px; font-family: "Fraunces", Georgia, serif; line-height: 1; }
  .headline__grand { display: block; margin-left: 26px; font-size: 20px; font-weight: 600; color: var(--ink); }
  .headline__opening { display: block; font-size: 31px; font-weight: 700; color: var(--orange); }

  .feature-image { position: absolute; left: 0; top: 190px; width: 255px; height: 145px; }
  .feature-image--shop { background: linear-gradient(180deg, #cfd3d6 0%, #e7e7e5 30%, #2b2b2b 52%, #8f8f8c 75%, #b9b7b2 100%); }
  .feature-image--sandwich { background: linear-gradient(160deg, #d8b58a 0%, #c9945f 35%, #d94a34 55%, #7fa24a 75%, #e9d9b8 100%); }

  .hours-badge {
    position: absolute; left: 163px; top: 272px; width: 84px; height: 84px; border-radius: 50%;
    background: var(--ink); border: 3px solid var(--white);
    display: flex; flex-direction: column; align-items: center; justify-content: center; text-align: center;
  }
  .hours-badge__time { font-family: "Open Sans", Arial, sans-serif; font-weight: 700; font-size: 13px; color: var(--orange); line-height: 1; }
  .hours-badge__text { font-size: 6.6px; color: var(--white); line-height: 1.2; margin-top: 2px; }

  .ownership { position: absolute; left: 20px; top: 326px; font-family: "Fraunces", Georgia, serif; font-style: italic; line-height: 1; }
  .ownership__women { display: block; font-size: 39px; font-weight: 800; color: var(--ink); letter-spacing: -.5px; }
  .ownership__family { display: block; font-size: 19px; font-weight: 700; color: var(--orange); margin-top: 1px; }
  .tagline { position: absolute; left: 16px; top: 392px; font-size: 11px; font-weight: 600; color: var(--ink); }

  .features { position: absolute; left: 0; top: 422px; width: 255px; height: 136px; display: grid; grid-template-columns: 1fr 1fr; grid-template-rows: 78px 58px; }
  .feature { display: flex; flex-direction: column; align-items: center; justify-content: center; text-align: center; color: var(--white); font-size: 8px; line-height: 1.3; padding: 0 6px; }
  .feature svg { width: 24px; height: 24px; margin-bottom: 4px; }

  .cta { position: absolute; left: 0; width: 255px; top: 566px; text-align: center; line-height: 1; }
  .cta__lead { display: block; font-size: 15px; color: var(--ink); }
  .cta__url { display: block; margin-top: 5px; font-family: "Fraunces", Georgia, serif; font-style: italic; font-weight: 800; font-size: 19px; color: var(--orange); }

  .caption { position: absolute; top: 781px; width: 300px; text-align: center; color: var(--label); font-size: 22px; letter-spacing: .5px; }
  .caption--pink { left: 308px; }
  .caption--white { left: 649px; }
</style>
</head>
<body>

<!-- Pink version -->
<article class="hanger hanger--pink">
  <svg class="hanger__shape" viewBox="0 0 255 660" aria-hidden="true">
    <defs>
      <radialGradient id="glowPink" cx="0.4" cy="0.35" r="0.7">
        <stop offset="0" stop-color="var(--paper-glow)"/>
        <stop offset="1" stop-color="var(--paper)"/>
      </radialGradient>
    </defs>
    <rect width="255" height="660" fill="var(--ink)"/>
    <path d="M0 0 H118 Q232 40 255 176 V632 Q128 640 0 630 Z" fill="url(#glowPink)"/>
    <path d="M0 418 Q60 410 128 414 T255 410 V556 Q130 566 0 560 Z" fill="var(--orange)"/>
    <line x1="128" y1="428" x2="128" y2="552" stroke="var(--rose)" stroke-width="0.8"/>
    <line x1="6" y1="500" x2="249" y2="500" stroke="var(--rose)" stroke-width="0.8"/>
    <rect x="0" y="73" width="100" height="58" fill="var(--stage)"/>
    <circle cx="128" cy="96" r="45" fill="var(--stage)"/>
  </svg>

  <div class="brand"><span class="brand__name">Marla’s</span><span class="brand__sub">Sandwich Corner</span></div>

  <h1 class="headline"><span class="headline__grand">Grand</span><span class="headline__opening">Opening</span></h1>

  <div class="feature-image feature-image--shop" role="img" aria-label="Photo of the shop front with its owners standing at the entrance"></div>

  <div class="hours-badge"><span class="hours-badge__time">7:00am</span><span class="hours-badge__text">Fresh Daily Grounded<br>Coffee<br>and Breakfast</span></div>

  <h2 class="ownership"><span class="ownership__women">women</span><span class="ownership__family">and family owned</span></h2>
  <p class="tagline">Handcrafted Sandwiches Made with Love</p>

  <ul class="features">
    <li class="feature">
      <svg viewBox="0 0 24 24" fill="none" stroke="#fff" stroke-width="1.4"><path d="M3 13 H21 L19 19 H5 Z"/><path d="M4 13 Q12 4 20 13"/><path d="M9 7 V5 M12 6 V3 M15 7 V5"/></svg>
      Fresh Baked Breadrafted<br>Sandwiches Made with Love
    </li>
    <li class="feature">
      <svg viewBox="0 0 24 24" fill="none" stroke="#fff" stroke-width="1.4"><path d="M5 11 H19 V17 Q19 20 16 20 H8 Q5 20 5 17 Z"/><path d="M3 11 H21"/><path d="M9 11 L12 7 L15 11"/><path d="M12 7 V4"/></svg>
      House-made Slow<br>Roasted House<br>Specialties
    </li>
    <li class="feature">
      <svg viewBox="0 0 24 24" fill="none" stroke="#fff" stroke-width="1.4"><circle cx="12" cy="12" r="10"/><path d="M12 6 V18 M12 9 L9 7 M12 9 L15 7 M12 13 L9 11 M12 13 L15 11"/><path d="M5 5 L19 19"/></svg>
      Gluten-Friendly
    </li>
    <li class="feature">
      <svg viewBox="0 0 24 24" fill="none" stroke="#fff" stroke-width="1.4"><path d="M5 19 Q4 6 19 5 Q20 18 5 19 Z"/><path d="M5 19 L14 10"/></svg>
      Vegan-Friendly
    </li>
  </ul>

  <p class="cta"><span class="cta__lead">Order Online at</span><span class="cta__url">MarlasCorner.example</span></p>
</article>

<!-- White version -->
<article class="hanger hanger--white">
  <svg class="hanger__shape" viewBox="0 0 255 660" aria-hidden="true">
    <defs>
      <radialGradient id="glowWhite" cx="0.4" cy="0.35" r="0.7">
        <stop offset="0" stop-color="var(--paper-glow)"/>
        <stop offset="1" stop-color="var(--paper)"/>
      </radialGradient>
    </defs>
    <rect width="255" height="660" fill="var(--ink)"/>
    <path d="M0 0 H118 Q232 40 255 176 V632 Q128 640 0 630 Z" fill="url(#glowWhite)"/>
    <path d="M0 418 Q60 410 128 414 T255 410 V556 Q130 566 0 560 Z" fill="var(--orange)"/>
    <line x1="128" y1="428" x2="128" y2="552" stroke="var(--rose)" stroke-width="0.8"/>
    <line x1="6" y1="500" x2="249" y2="500" stroke="var(--rose)" stroke-width="0.8"/>
    <rect x="0" y="73" width="100" height="58" fill="var(--stage)"/>
    <circle cx="128" cy="96" r="45" fill="var(--stage)"/>
  </svg>

  <div class="brand"><span class="brand__name">Marla’s</span><span class="brand__sub">Sandwich Corner</span></div>

  <h1 class="headline"><span class="headline__grand">Grand</span><span class="headline__opening">Opening</span></h1>

  <div class="feature-image feature-image--sandwich" role="img" aria-label="Photo of a grilled panini with tomato, mozzarella, basil and lettuce"></div>

  <div class="hours-badge"><span class="hours-badge__time">7:00am</span><span class="hours-badge__text">Fresh Daily Grounded<br>Coffee<br>and Breakfast</span></div>

  <h2 class="ownership"><span class="ownership__women">women</span><span class="ownership__family">and family owned</span></h2>
  <p class="tagline">Handcrafted Sandwiches Made with Love</p>

  <ul class="features">
    <li class="feature">
      <svg viewBox="0 0 24 24" fill="none" stroke="#fff" stroke-width="1.4"><path d="M3 13 H21 L19 19 H5 Z"/><path d="M4 13 Q12 4 20 13"/><path d="M9 7 V5 M12 6 V3 M15 7 V5"/></svg>
      Fresh Baked Breadrafted<br>Sandwiches Made with Love
    </li>
    <li class="feature">
      <svg viewBox="0 0 24 24" fill="none" stroke="#fff" stroke-width="1.4"><path d="M5 11 H19 V17 Q19 20 16 20 H8 Q5 20 5 17 Z"/><path d="M3 11 H21"/><path d="M9 11 L12 7 L15 11"/><path d="M12 7 V4"/></svg>
      House-made Slow<br>Roasted House<br>Specialties
    </li>
    <li class="feature">
      <svg viewBox="0 0 24 24" fill="none" stroke="#fff" stroke-width="1.4"><circle cx="12" cy="12" r="10"/><path d="M12 6 V18 M12 9 L9 7 M12 9 L15 7 M12 13 L9 11 M12 13 L15 11"/><path d="M5 5 L19 19"/></svg>
      Gluten-Friendly
    </li>
    <li class="feature">
      <svg viewBox="0 0 24 24" fill="none" stroke="#fff" stroke-width="1.4"><path d="M5 19 Q4 6 19 5 Q20 18 5 19 Z"/><path d="M5 19 L14 10"/></svg>
      Vegan-Friendly
    </li>
  </ul>

  <p class="cta"><span class="cta__lead">Order Online at</span><span class="cta__url">MarlasCorner.example</span></p>
</article>

<p class="caption caption--pink">PINK BACKGROUND</p>
<p class="caption caption--white">WHITE BACKGROUND</p>

</body>
</html>
```